Business Card Design

We need a business card designed for our new company. Prefer a black card with white logo & writing.

Contact Information for Business Card

Ted Galloway, address: 7-4812 Fernhollow Road, Abbotsford, BC, V3K 8R2, Office Phone: 604-712-3390, Cell: 604-947-2164, Email: ted@resinworkshub.ca

Colors

Designer to choose only greyscale colors for use in the design.

```html
<!DOCTYPE html>
<html lang="en">
<head>
<meta charset="utf-8">
<title>Resinworks Hub — Business Card</title>
<link rel="stylesheet" href="https://fonts.googleapis.com/css2?family=Montserrat:wght@400;500;700;800&display=swap">
<style>
  :root {
    --canvas: #d9d9d9;
    --card-black: #1f1f1f;
    --card-white: #ffffff;
    --ink: #111111;
    --ink-soft: #2b2b2b;
    --ink-muted: #555555;
    --on-dark: #ffffff;
  }
  * { box-sizing: border-box; margin: 0; padding: 0; }
  html, body { width: 1200px; height: 786px; overflow: hidden; }
  body {
    background: var(--canvas);
    font-family: "Montserrat", sans-serif;
    display: flex;
    align-items: center;
    justify-content: center;
    gap: 48px;
  }
  .card {
    width: 540px;
    height: 309px;
    position: relative;
    overflow: hidden;
    box-shadow: 0 6px 18px rgba(0,0,0,0.25);
  }
  /* Front: contact side */
  .card--front { display: flex; }
  .contact-panel {
    width: 47%;
    background: var(--card-white);
    color: var(--ink);
    padding: 40px 0 0 34px;
  }
  .contact-name { font-weight: 800; font-size: 19px; letter-spacing: 0.2px; }
  .contact-role { font-size: 10px; color: var(--ink-muted); margin: 6px 0 0 10px; }
  .contact-address {
    font-size: 11.5px;
    line-height: 1.3;
    color: var(--ink-soft);
    margin-top: 74px;
  }
  .contact-list { list-style: none; margin-top: 10px; }
  .contact-list li {
    display: flex;
    align-items: center;
    gap: 10px;
    font-size: 11.5px;
    color: var(--ink-soft);
    line-height: 1;
    margin-bottom: 8px;
  }
  .contact-list svg { width: 11px; height: 11px; flex: none; }
  .brand-panel {
    flex: 1;
    background: var(--card-black);
    display: flex;
    align-items: center;
    justify-content: center;
  }
  /* Back: brand side */
  .card--back {
    background: var(--card-black);
    display: flex;
    align-items: center;
    justify-content: center;
  }
  .brand {
    display: flex;
    align-items: center;
    gap: 10px;
    color: var(--on-dark);
    font-weight: 800;
    text-transform: uppercase;
    letter-spacing: 0.5px;
  }
  .brand-dot {
    border-radius: 50%;
    background: var(--on-dark);
    flex: none;
  }
  .brand--small { font-size: 19px; }
  .brand--small .brand-dot { width: 12px; height: 12px; }
  .brand--large { font-size: 30px; }
  .brand--large .brand-dot { width: 18px; height: 18px; }
</style>
</head>
<body>

  <section class="card card--front" aria-label="Business card, contact side">
    <div class="contact-panel">
      <h1 class="contact-name">Ted Galloway</h1>
      <p class="contact-role">owner</p>
      <p class="contact-address">7-4812 Fernhollow Road,<br>Abbotsford, BC, V3K 8R2</p>
      <ul class="contact-list">
        <li>
          <svg viewBox="0 0 12 12" aria-hidden="true"><path d="M2.5 1 L4.5 1 L5.2 3.4 L3.9 4.4 Q5 6.9 7.6 8.1 L8.6 6.8 L11 7.5 L11 9.5 Q10.8 11 9.3 11 Q1 10.2 1 2.7 Q1 1.2 2.5 1 Z" fill="var(--ink)"/></svg>
          604-712-3390
        </li>
        <li>
          <svg viewBox="0 0 12 12" aria-hidden="true"><rect x="3" y="0.6" width="6" height="10.8" rx="1.2" fill="none" stroke="var(--ink)" stroke-width="1.1"/><circle cx="6" cy="9.6" r="0.6" fill="var(--ink)"/></svg>
          604-947-2164
        </li>
        <li>
          <svg viewBox="0 0 12 12" aria-hidden="true"><rect x="0.5" y="2.2" width="11" height="7.6" fill="var(--ink)"/><path d="M0.8 2.6 L6 6.6 L11.2 2.6" fill="none" stroke="var(--card-white)" stroke-width="0.9"/></svg>
          ted@resinworkshub.ca
        </li>
        <li>
          <svg viewBox="0 0 12 12" aria-hidden="true"><circle cx="6" cy="6" r="5.4" fill="var(--ink)"/><path d="M3 4 Q5 3 5.5 5 Q4 7 6 8.5 M7.5 2 Q9 4 8 6" fill="none" stroke="var(--card-white)" stroke-width="0.9"/></svg>
          www.resinworkshub.ca
        </li>
      </ul>
    </div>
    <div class="brand-panel">
      <div class="brand brand--small"><span class="brand-dot"></span>Resinworks Hub</div>
    </div>
  </section>

  <section class="card card--back" aria-label="Business card, brand side">
    <div class="brand brand--large"><span class="brand-dot"></span>Resinworks Hub</div>
  </section>

</body>
</html>
```